Header/Banner Design for Website

Looking for a banner/header design for www.nestfixerdiaries.net Should be fun and whimsical, and include the name of the website, something to do with home improvement or tools, and a caricature of a young, beautiful 20 something blond who the website revolves around. The website is about a young woman who bought her first house and it taking on all of the renovations and remodeling on her own for the first time.

The header/banner should include the same colors that are in the website. The width should be no more than 430 pixels, the height is flexible but the current space in the header is 85 pixels...looking for some creativity. any questions, please ask. Attached an image that she liked for the image of the woman (would like to see versions of this included)
Updates

Target Market(s)

women 20+ that are new home owners or that are tackling home improvement on their own

Industry/Entity Type

Home Improvement

Requirements
Must have
• color coordinate with the website
should feature a young, blond, female caricature
should include the name of the website

```html
<!DOCTYPE html>
<html lang="en">
<head>
<meta charset="utf-8">
<title>Nest Fixer Diaries – Header Banner</title>
<link rel="stylesheet" href="https://fonts.googleapis.com/css2?family=Open+Sans:wght@700&family=Roboto+Condensed:wght@700&display=swap">
<style>
  :root {
    --backdrop: #e9e6e2;
    --banner-light: #fde6e1;
    --banner-mid: #fbd3c8;
    --banner-deep: #f8c0b0;
    --nav-plum: #6b1342;
    --nav-text: #ffffff;
    --brand-plum: #7a1d4f;
    --brand-magenta: #c21f7a;
    --figure-top: #f6d3b4;
    --figure-mid: #f0a6c6;
    --figure-base: #d94a8c;
  }
  * { margin: 0; padding: 0; box-sizing: border-box; }
  html, body {
    width: 1200px;
    height: 900px;
    overflow: hidden;
    background: var(--backdrop);
  }
  .header-banner {
    position: absolute;
    left: 29px;
    top: 348px;
    width: 1151px;
    height: 187px;
    border-radius: 0 0 16px 16px;
    overflow: hidden;
    box-shadow: 0 3px 10px rgba(0, 0, 0, 0.18);
  }
  .banner-top {
    position: absolute;
    left: 0;
    top: 0;
    width: 100%;
    height: 141px;
    background: linear-gradient(90deg, var(--banner-light) 0%, var(--banner-mid) 55%, var(--banner-deep) 100%);
  }
  .mascot-area {
    position: absolute;
    left: 73px;
    top: 4px;
    width: 92px;
    height: 137px;
    background: linear-gradient(180deg, var(--figure-top) 0%, var(--figure-mid) 45%, var(--figure-base) 100%);
    opacity: 0.85;
  }
  .brand {
    position: absolute;
    left: 196px;
    top: 56px;
    display: flex;
    align-items: center;
    gap: 12px;
  }
  .brand-mark {
    width: 30px;
    height: 30px;
    background: var(--brand-magenta);
  }
  .brand-name {
    font-family: "Roboto Condensed", sans-serif;
    font-weight: 700;
    font-size: 40px;
    line-height: 1;
    color: var(--brand-plum);
    letter-spacing: 0.2px;
  }
  .main-nav {
    position: absolute;
    left: 0;
    bottom: 0;
    width: 100%;
    height: 46px;
    background: var(--nav-plum);
  }
  .nav-item {
    position: absolute;
    top: 50%;
    transform: translate(-50%, -50%);
    font-family: "Open Sans", sans-serif;
    font-weight: 700;
    font-size: 17px;
    color: var(--nav-text);
    white-space: nowrap;
  }
</style>
</head>
<body>
  <header class="header-banner">
    <div class="banner-top">
      <div class="mascot-area" role="img" aria-label="Caricature of a young blond woman in pink overalls holding a power drill"></div>
      <div class="brand">
        <span class="brand-mark" aria-hidden="true"></span>
        <span class="brand-name">Nest Fixer Diaries</span>
      </div>
    </div>
    <nav class="main-nav">
      <span class="nav-item" style="left:95px">About Us</span>
      <span class="nav-item" style="left:286px">Products</span>
      <span class="nav-item" style="left:478px">Completed Projects</span>
      <span class="nav-item" style="left:669px">Share Your Projects</span>
      <span class="nav-item" style="left:861px">Articles</span>
      <span class="nav-item" style="left:1051px">How to Resources</span>
    </nav>
  </header>
</body>
</html>
```